Trade Show Marlow 3x3 booth schel scheme

We would like to have full coverage design for 3x3 booth scheel

2x2 pop up Counter (1200mm wide x 900mm high x 400mm deep)
Our company provides food safety training, consultancy and food safety app service for hospitality businesses.

```html
<!DOCTYPE html>
<html lang="en">
<head>
<meta charset="utf-8">
<title>Verdan – Trade Show Booth Graphics</title>
<link rel="stylesheet" href="https://fonts.googleapis.com/css2?family=Anton&family=Oswald:wght@300&family=Great+Vibes&family=Montserrat:wght@500&display=swap">
<style>
  :root {
    --stage: #d6d6d6;
    --cream: #fafbe3;
    --cream-text: #fbfce8;
    --lime: #c8d530;
    --leaf: #7f9a1c;
    --ink: #151515;
    --orange: #f39a3a;
    --carrot: #f2a35e;
    --shadow: rgba(0,0,0,0.28);
  }
  * { box-sizing: border-box; margin: 0; padding: 0; }
  html, body { width: 817px; height: 1200px; overflow: hidden; }
  body { background: var(--stage); position: relative; font-family: "Anton", sans-serif; }

  .panel {
    position: absolute;
    width: 363px; height: 363px;
    background: var(--cream);
    overflow: hidden;
    box-shadow: 0 10px 14px -6px var(--shadow);
  }
  .panel--rating { left: 36px; top: 170px; }
  .panel--promise { left: 418px; top: 170px; }
  .blob { position: absolute; inset: 0; width: 100%; height: 100%; }
  .blob path { fill: var(--lime); }

  .art { position: absolute; border-radius: 40%; }
  .art--plate { left: 11px; top: 25px; width: 116px; height: 96px; background: radial-gradient(circle at 50% 45%, #b9c94a 0 30%, #e8edc8 31% 60%, rgba(200,213,48,0.35) 61%); }
  .art--spinach-left { left: 22px; top: 225px; width: 88px; height: 80px; background: radial-gradient(circle, #9bb52c, #6f8f1f 70%, rgba(111,143,31,0.3)); }
  .art--carrot-bread { left: 14px; top: 95px; width: 108px; height: 130px; background: linear-gradient(140deg, var(--carrot), #f6c08a 60%, #d2dd6a); }
  .art--spinach-right { left: 276px; top: 170px; width: 76px; height: 80px; background: radial-gradient(circle, #9bb52c, #6f8f1f 70%, rgba(111,143,31,0.3)); }

  .script { position: absolute; left: 141px; top: 42px; font-family: "Great Vibes", cursive; color: var(--ink); font-size: 28px; line-height: 1; white-space: nowrap; }
  .headline { position: absolute; left: 141px; top: 78px; color: var(--cream-text); font-size: 48px; line-height: 0.9; text-transform: uppercase; font-weight: 400; }
  .subline { position: absolute; left: 141px; top: 212px; color: var(--ink); font-size: 34px; line-height: 1.02; text-transform: uppercase; }

  .promise-intro { position: absolute; left: 134px; top: 22px; font-family: "Oswald", sans-serif; font-weight: 300; color: var(--cream-text); font-size: 30px; line-height: 1; letter-spacing: -0.5px; white-space: nowrap; }
  .promise-head { position: absolute; left: 134px; top: 62px; color: var(--cream-text); font-size: 60px; line-height: 0.98; text-transform: uppercase; font-weight: 400; white-space: nowrap; }
  .promise-head .bang { color: var(--leaf); display: inline-block; transform: rotate(6deg); }

  .wordmark { font-family: "Montserrat", sans-serif; font-weight: 500; letter-spacing: 0.28em; white-space: nowrap; }
  .panel--promise .wordmark { position: absolute; left: 141px; top: 296px; font-size: 32px; color: var(--ink); }

  .dot { position: absolute; border-radius: 50%; }
  .dot--o { background: var(--orange); }
  .dot--g { background: var(--lime); }

  .sign {
    position: absolute;
    background: var(--ink);
    overflow: hidden;
    box-shadow: 0 10px 14px -6px var(--shadow);
    color: #fff;
  }
  .sign--hanging { left: 36px; top: 570px; width: 363px; height: 363px; }
  .sign--counter { left: 418px; top: 616px; width: 363px; height: 272px; }
  .sign .art--leaves { top: 0; left: 22px; width: 110px; height: 62px; background: radial-gradient(circle, #b6c844, #7f9a1c 70%, rgba(127,154,28,0.2)); }
  .sign .art--avocado { border-radius: 45%; background: radial-gradient(circle at 60% 60%, var(--orange) 0 18%, #d9e07a 19% 45%, #7f9a1c 70%); }
  .sign .wordmark { position: absolute; left: 0; right: 0; text-align: center; color: #fff; }
  .tagline { position: absolute; left: 0; right: 0; text-align: center; text-transform: uppercase; line-height: 1.05; }
  .tagline .hl { color: var(--lime); }
  .sign--hanging .wordmark { top: 112px; font-size: 36px; }
  .sign--hanging .tagline { top: 172px; font-size: 38px; padding-left: 30px; }
  .sign--hanging .art--avocado { left: 22px; top: 262px; width: 60px; height: 78px; }
  .sign--counter .wordmark { top: 68px; font-size: 32px; }
  .sign--counter .tagline { top: 120px; font-size: 34px; padding-left: 30px; }
  .sign--counter .art--avocado { left: 16px; top: 198px; width: 52px; height: 66px; }
</style>
</head>
<body>

  <section class="panel panel--rating">
    <svg class="blob" viewBox="0 0 100 100" preserveAspectRatio="none" aria-hidden="true">
      <path d="M53 0 H100 V80 C92 90 75 95 60 93 C48 96 38 92 33 84 C22 75 20 60 24 48 C22 38 26 30 33 28 C38 20 42 8 53 0 Z"/>
    </svg>
    <div class="art art--plate" role="img" aria-label="Illustration of a plate with a tick, fork and knife"></div>
    <div class="art art--spinach-left" role="img" aria-label="Illustration of spinach leaves"></div>
    <p class="script">Achieve &amp; Maintain</p>
    <h2 class="headline">5 Star<br>Hygiene<br>Rating</h2>
    <p class="subline">With experts<br>at your side</p>
  </section>

  <section class="panel panel--promise">
    <svg class="blob" viewBox="0 0 100 100" preserveAspectRatio="none" aria-hidden="true">
      <path d="M30 0 H100 V58 C95 68 85 70 75 68 C65 72 55 70 47 64 C40 68 32 66 28 60 C22 55 22 48 25 43 C17 40 14 30 18 24 C20 18 26 15 32 17 C33 10 30 5 30 0 Z"/>
    </svg>
    <div class="art art--carrot-bread" role="img" aria-label="Illustration of a carrot and bread loaf with a tick badge"></div>
    <div class="art art--spinach-right" role="img" aria-label="Illustration of spinach leaves"></div>
    <span class="dot dot--o" style="left:36px;top:32px;width:7px;height:7px"></span>
    <span class="dot dot--o" style="left:62px;top:26px;width:5px;height:5px"></span>
    <span class="dot dot--g" style="left:48px;top:42px;width:4px;height:4px"></span>
    <span class="dot dot--o" style="left:52px;top:48px;width:6px;height:6px"></span>
    <span class="dot dot--o" style="left:52px;top:246px;width:10px;height:10px"></span>
    <span class="dot dot--g" style="left:55px;top:266px;width:6px;height:6px"></span>
    <span class="dot dot--o" style="left:86px;top:266px;width:9px;height:9px"></span>
    <span class="dot dot--o" style="left:40px;top:287px;width:9px;height:9px"></span>
    <span class="dot dot--g" style="left:66px;top:284px;width:5px;height:5px"></span>
    <p class="promise-intro">Our Promise Is</p>
    <h2 class="promise-head">Peace of<br>Mind<span class="bang">!</span></h2>
    <p class="wordmark">VERDAN</p>
  </section>

  <section class="sign sign--hanging">
    <div class="art art--leaves" role="img" aria-label="Illustration of green leaves"></div>
    <span class="dot dot--g" style="left:298px;top:32px;width:7px;height:7px"></span>
    <span class="dot dot--g" style="left:320px;top:28px;width:6px;height:6px"></span>
    <span class="dot dot--g" style="left:326px;top:46px;width:5px;height:5px"></span>
    <p class="wordmark">VERDAN</p>
    <p class="tagline">Food <span class="hl">Hygiene</span><br><span class="hl">Health</span> Safety</p>
    <div class="art art--avocado" role="img" aria-label="Illustration of a halved avocado with a tick badge"></div>
    <span class="dot dot--o" style="left:322px;top:272px;width:7px;height:7px"></span>
    <span class="dot dot--o" style="left:304px;top:290px;width:6px;height:6px"></span>
    <span class="dot dot--g" style="left:326px;top:298px;width:5px;height:5px"></span>
    <span class="dot dot--o" style="left:292px;top:312px;width:6px;height:6px"></span>
    <span class="dot dot--o" style="left:336px;top:316px;width:7px;height:7px"></span>
  </section>

  <section class="sign sign--counter">
    <div class="art art--leaves" role="img" aria-label="Illustration of green leaves"></div>
    <span class="dot dot--g" style="left:310px;top:24px;width:7px;height:7px"></span>
    <span class="dot dot--g" style="left:332px;top:38px;width:6px;height:6px"></span>
    <p class="wordmark">VERDAN</p>
    <p class="tagline">Food <span class="hl">Hygiene</span><br><span class="hl">Health</span> Safety</p>
    <div class="art art--avocado" role="img" aria-label="Illustration of a halved avocado with a tick badge"></div>
    <span class="dot dot--o" style="left:330px;top:196px;width:7px;height:7px"></span>
    <span class="dot dot--g" style="left:312px;top:216px;width:6px;height:6px"></span>
    <span class="dot dot--o" style="left:336px;top:232px;width:7px;height:7px"></span>
    <span class="dot dot--o" style="left:300px;top:240px;width:6px;height:6px"></span>
  </section>

</body>
</html>
```